Tjirpsa car advertisement

de website moet uit minimaal 3 pagina's bestaan. 1 pagina als een landingspagina. 1 pagina voor consumenten die hun auto willen laten beplakken met bedrijfsreclame en 1 pagina voor bedrijven / consumenten die hun bedrijfsreclame op een consumentenauto wilt plaatsen.

de website moet echt een happy website zijn. consumenten kunnen geld verdienen met reclame op hun auto te laten zetten en bedrijven kunnen voor een relatief goedkoop bedrag hun bedrijfsreclame op een auto laten zetten. die auto rijdt dan rond en veel mensen zien de reclame.

beide pagina's moeten dus een glimlach opleveren.

het doel van de startpagina is dat je door kunt gaan naar de consumenten en de bedrijfspagina.

gebruik leuke, vrolijke kleuren en vormen en zorg dat de mensen een glimlach krijgen als ze naar de website kijken.

doelgroep is consumenten die een auto rijden en geld willen verdienen met hun auto en de zakelijke ondernemer die voor een goedkoop bedrag zijn bedrijfsreclame met een full carwrap kan laten zien aan de buitenwereld.

doordat consumenten zich bij ons aanmelden hebben wij een database met auto's en weten we hoeveel deze auto's rijden en in welke regio's ze rijden en wat voor auto ze rijden. allemaal hele belangrijke informatie voor een ondernemer die reclame wilt maken op ene specifieke auto type en in een bepaalde regio.

-

website should consist of at least 3 pages. 1 landing page, 1 customer page and 1 business page. landing page let's the visitor choose wether he / she is a customer with a car and wants to allow his car to be fully carwrapped or he / she is a business owner who wants to place his advertisement on a car.

website should be a really happy joyfull website and bring a smile to the visitor. beause the customer can earn money (200 euro / month nett) by allowing advertisements on his car (full car wrap) and the business owner because for a low price he can advertise.

when customers that owns a car register themselves with our website we build a database with cars in specific locations. a business owner wants to advertise his product into a specific region. this is very valuable information.

agreement is 1 year for a customer to have advertisements on his car and for a business to advertise. after that year, the advertisements are safely removed from the car and new advertisement agreements can be made. a business can place advertisements (full carwrap) already for 795 euro's., Details for my new Web Design Project will be added soon. , de website moet uit minimaal 3 pagina's bestaan. 1 pagina als een landingspagina. 1 pagina voor consumenten die hun auto willen laten beplakken met bedrijfsreclame en 1 pagina voor bedrijven / consumenten die hun bedrijfsreclame op een consumentenauto wilt plaatsen.

Target Market(s)

customers who has a car
businesses who want to advertise their business / product on a car

Industry/Entity Type

Business

Requirements
Must have
• website should be playfull, colorfull and a joy to look at and work with. altough functoinality is very limited visitors need to be intrigued to proceed to contact tjirpsa.
Nice to have
• nice graphics, moving images, a "living" website (not so static)

```html
<!DOCTYPE html>
<html lang="en">
<head>
<meta charset="utf-8">
<title>Tjirpsa – Car advertisement</title>
<link rel="stylesheet" href="https://fonts.googleapis.com/css2?family=Arimo:wght@400;700&display=swap">
<style>
  :root {
    --orange: #f7931e;
    --red: #d8262c;
    --white: #ffffff;
    --nav-text: #8a8a8a;
    --panel-dark: rgba(10, 10, 10, 0.82);
    --caption-dark: rgba(40, 40, 40, 0.72);
    --rule: rgba(255, 255, 255, 0.55);
    --quote: #777777;
    --input: #ececec;
  }
  * { margin: 0; padding: 0; box-sizing: border-box; }
  html, body { width: 1200px; height: 628px; overflow: hidden; }
  body {
    position: relative;
    font-family: "Arimo", Arial, sans-serif;
    color: var(--white);
    background: #2a2622;
  }
  .hero-photo {
    position: absolute; inset: 0;
    background:
      radial-gradient(ellipse 55% 60% at 58% 45%, #c9c1b2 0%, #a59c8b 45%, transparent 75%),
      radial-gradient(ellipse 30% 50% at 95% 55%, #b4551f 0%, transparent 70%),
      linear-gradient(100deg, #2b2a24 0%, #4a463c 18%, #8d8576 40%, #9f9684 65%, #5a4030 88%, #3a2418 100%);
  }
  .slider-controls {
    position: absolute; top: 8px; right: 8px;
    display: flex; gap: 10px; align-items: center;
  }
  .logo {
    position: absolute; left: 144px; top: 26px;
    font-size: 32px; font-weight: 700; color: var(--orange);
    letter-spacing: 0.5px;
  }
  .top-tools {
    position: absolute; left: 911px; top: 16px; width: 145px; height: 46px;
    background: rgba(30, 30, 30, 0.55);
    border-bottom: 2px solid rgba(255,255,255,0.6);
    display: flex; align-items: center; justify-content: flex-end; gap: 6px;
    padding-right: 10px;
  }
  .top-tools .divider { width: 1px; height: 18px; background: rgba(255,255,255,0.5); margin: 0 6px; }
  .social-dot { width: 14px; height: 14px; background: var(--white); border-radius: 2px; }
  .main-nav {
    position: absolute; left: 144px; top: 69px; width: 599px; height: 76px;
    background: rgba(255, 255, 255, 0.9);
    display: flex;
  }
  .main-nav a {
    display: flex; align-items: center; padding: 0 14px;
    font-size: 13px; color: var(--nav-text); text-decoration: none;
  }
  .main-nav a.active { background: var(--orange); color: var(--white); width: 61px; justify-content: center; padding: 0; }
  .testimonial {
    position: absolute; left: 743px; top: 69px; width: 313px; height: 76px;
    background: var(--white);
    padding: 14px 10px 0 10px;
    border-top: 5px solid #e8e8e8;
  }
  .testimonial h4 { font-size: 10px; font-weight: 400; color: var(--orange); margin-top: -4px; }
  .testimonial blockquote { font-size: 11.5px; font-style: italic; color: var(--quote); line-height: 12px; margin-top: 2px; }
  .testimonial cite { display: block; font-size: 10px; font-style: normal; color: #333; margin-top: 3px; }
  .hero-caption { position: absolute; left: 144px; top: 217px; }
  .hero-caption h1 {
    display: inline-block; background: var(--caption-dark);
    font-size: 29px; font-weight: 400; padding: 4px 13px 5px 13px; height: 41px;
  }
  .hero-caption p {
    display: inline-block; background: var(--caption-dark);
    font-size: 13.5px; padding: 6px 13px; margin-top: 3px; height: 30px;
  }
  .view-more {
    display: block; width: 94px; height: 32px; margin-top: 9px;
    background: var(--red); color: var(--white); font-size: 12px;
    text-align: center; line-height: 32px; text-decoration: none;
  }
  .site-footer {
    position: absolute; left: 144px; top: 445px; width: 912px; height: 163px;
    background: var(--panel-dark);
  }
  .footer-col { position: absolute; top: 20px; width: 266px; font-size: 11.5px; line-height: 16px; }
  .footer-col h3 {
    font-size: 20px; font-weight: 400; padding-bottom: 5px;
    border-bottom: 1px solid var(--rule); margin-bottom: 5px;
  }
  .col-about { left: 19px; }
  .col-contact { left: 323px; }
  .col-news { left: 627px; }
  .world-map {
    position: absolute; left: 30px; top: 52px; width: 170px; height: 90px;
    background: radial-gradient(ellipse at center, rgba(200,200,200,0.45), rgba(200,200,200,0) 70%);
  }
  .contact-lines { position: relative; }
  .contact-line { display: flex; align-items: center; gap: 4px; }
  .copyright { position: absolute; left: 19px; top: 140px; font-size: 8px; }
  .subscribe { display: flex; margin-top: 9px; }
  .subscribe input { width: 133px; height: 24px; border: 0; background: var(--input); }
  .subscribe button {
    width: 67px; height: 24px; border: 0; background: var(--orange); color: var(--white);
    font-family: "Arimo", Arial, sans-serif; font-size: 11.5px;
  }
</style>
</head>
<body>
  <div class="hero-photo" role="img" aria-label="Close-up photo of a white car side wrapped with a company advertisement"></div>

  <div class="slider-controls">
    <svg width="22" height="20" viewBox="0 0 22 20" fill="none" stroke="rgba(255,255,255,0.6)" stroke-width="2">
      <path d="M1 6V1h6M15 1h6v5M21 14v5h-6M7 19H1v-5"/>
    </svg>
    <svg width="18" height="22" viewBox="0 0 18 22"><path d="M1 1l16 10L1 21z" fill="rgba(255,255,255,0.6)"/></svg>
    <svg width="40" height="22" viewBox="0 0 40 22" fill="none" stroke="rgba(255,255,255,0.6)" stroke-width="2.5">
      <path d="M14 1L3 11l11 10M26 1l11 10-11 10"/>
    </svg>
  </div>

  <div class="logo">Tjirpsa</div>

  <div class="top-tools">
    <svg width="16" height="11" viewBox="0 0 16 11"><rect width="16" height="4" fill="#c8102e"/><rect y="4" width="16" height="3" fill="#fff"/><rect y="7" width="16" height="4" fill="#1e3f8f"/></svg>
    <svg width="16" height="11" viewBox="0 0 16 11"><rect width="16" height="11" fill="#2a3f7f"/><rect x="6" width="4" height="11" fill="#fff"/><rect y="4" width="16" height="3" fill="#fff"/><rect x="7" width="2" height="11" fill="#c8102e"/><rect y="5" width="16" height="1" fill="#c8102e"/></svg>
    <span class="divider"></span>
    <span class="social-dot"></span>
    <span class="social-dot"></span>
    <span class="social-dot"></span>
  </div>

  <nav class="main-nav">
    <a class="active" href="#">Home</a>
    <a href="#">Car Holders</a>
    <a href="#">Business Holders</a>
    <a href="#">Advertisers</a>
    <a href="#">Our Works</a>
    <a href="#">Contact</a>
  </nav>

  <aside class="testimonial">
    <h4>Testimonials</h4>
    <blockquote>"Duis in jus letalis pagus patria verto. Duis eligo facilisis ideo nostrud paratus ulciscor."</blockquote>
    <cite>Sanne Visser</cite>
  </aside>

  <section class="hero-caption">
    <h1>Advertisers</h1><br>
    <p>For advertisers who want to place their client's advertisement on a car</p>
    <a class="view-more" href="#">VIEW MORE</a>
  </section>

  <footer class="site-footer">
    <div class="footer-col col-about">
      <h3>About us</h3>
      <p>Duis in jus letalis pagus patria verto. Duis eligo facilisis ideo nostrud paratus ulciscor. Duis in jus letalis pagus patria verto.</p>
    </div>
    <div class="footer-col col-contact">
      <div class="world-map" role="img" aria-label="Faint world map"></div>
      <h3>Contact us</h3>
      <div class="contact-lines">
        <p>Street Address<br>Locality, Region, Netherlands</p>
        <p class="contact-line" style="margin-top:5px">
          <svg width="10" height="14" viewBox="0 0 10 14" fill="none" stroke="#fff" stroke-width="1.4"><rect x="1" y="1" width="8" height="12" rx="1"/><path d="M4 11h2"/></svg>
          +31-000-00000
        </p>
        <p class="contact-line">
          <svg width="13" height="9" viewBox="0 0 13 9"><rect width="13" height="9" fill="#fff"/><path d="M0 0l6.5 5L13 0" fill="none" stroke="#222" stroke-width="1"/></svg>
          contact@tjirpsa.nl
        </p>
      </div>
    </div>
    <div class="footer-col col-news">
      <h3>Newsletter</h3>
      <p>Stay informed on our latest news!</p>
      <form class="subscribe"><input type="text" aria-label="Email"><button type="button">Subscribe</button></form>
    </div>
    <p class="copyright">© 2013 Tjirpsa. All rights reserved</p>
  </footer>
</body>
</html>
```